Website Redesign Project

Brightwater Delivery Partners provides project management and project controls consultancy services to companies in many industry sectors, within Australia and overseas. My company has been developing a business brand through forging strong business relationships within industry. We provide innovative tools, concepts and solutions to management teams to assist them in better plan and managing there project portfolios.
SECTORS OF INDUSTRY WE SERVICE
★Oil & Gas
★Minerals & Metals
★Petrochemical
★Manufacturing
★Building & Construction
★Telecommunications
★Rail
★Civil
OLD WEBSITE
My old website www.brightwaterdeliverypartners-demo.com.au needs a complete overhaul in terms of how the web pages look and feel. I am trying to get away from the grey, washed out look as it is uninviting and dull. My clients commented that my webpage does not reflect who I am as a company or my core values. Think total redesign
DESIGN
I would like a webpage design that is modern and has a corporate image. It must be elegant, classy, and have an overall glossy appearance. I want something exciting that creates some excellent feedback from clients. It needs to have a savvy appearance and an attitude of a market leader. A generic website template cannot be used as I provide a unique service to clients. I do not need a website design that looks like my compeditors, I want something that stands out in the crowd and effectivly markets my bussinesses brand. I want my website to represent quality, so only high resolution images that are clear, sharp and in focus can be used. With this design, throw your standard webpage design concepts out the window, as I want something fresh, innovative, exciting and inviting. The overall design should appear uncluttered as all content needs to be there for a reason, so think functional.
It must be professional and of the highest calibre as my clients expect nothing less. I provide clients with innovative tools, concepts and solutions, so the design needs to be edgy and creative to align with my company’s core business services. The new design must promote the company’s brand and us as a market leader. It must communicate that we service many industry sectors and reflect our company’s creativity, vision, energy and drive.
WEBPAGE WRITTEN CONTENT
I am happy with the written content on each page within my old website. You may arrange the text how you see fit within the new design. On the main page of my old website the text is under scored, I am not a big fan of this. I currently do not like the format the text is in, I am looking for a formatt that is easy to read, looks flattering and pleasing to the eye.
MAIN PAGE DESIGN
The main page design needs to focus on my company as a brand, it must promote that I service many industry sectors. My old webpage had me pigeon holed as only providing services to oil and gas. This is incorrect as I service oil & gas, metals and minerals, Petrochemical, Manufacturing, Building & Construction, Telecommunications, Rail and civil.
WEBPAGE COLUR PREFERENCE
Prefer a white background with plenty of colour
TESTIMONIAL TAB
The testimonial tab on the task bar can be removed as it is no longer required.
FINISHED PRODUCT
The finished product will be uploaded by you to a nominated web hosting account. I will need a copy of all files associated with the design. A copy of the finished product will also be provided in formats that can me imported to Xara Pro Designer as I will update my website in 6 months or so using this tool.
Updates
I have updated the design brief after recieving feedback from several designers
Thanks
Reason: Some designers have asked for more time
Hi All
I have just launched another project called "brightwater delivery partners business card redesign project", you are all welcome to join this project.
Thanks
Target Market(s)
★Oil and Gas
★Mining and Resources
★Building and infrastructure
★Petrochemical
★Civil and roads
★Rail
Industry/Entity Type
Industry
Requirements
Must have
- ★Draw you in
★Hold your attention
★Identify company brand
★Highlight skills experience and expertise
★Be a unique design not generic
Should not have
- ★The webpage design should not be old fashioned
★ The design should not be based off a generic design template
★The webpage should not be cluttered; everything needs to be there for a reason.

```html
<!DOCTYPE html>
<html lang="en">
<head>
<meta charset="utf-8">
<title>Brightwater Delivery Partners</title>
<link href="https://fonts.googleapis.com/css2?family=Open+Sans:wght@400;600;700;800&family=PT+Sans+Narrow:wght@400;700&display=swap" rel="stylesheet">
<style>
:root{
  --red:#c4161c;
  --red-dark:#9e0f14;
  --red-light:#e0262b;
  --ink:#222;
  --text:#555;
  --rule:#444;
  --footer-top:#2e2e2e;
  --footer-bottom:#0d0d0d;
  --sky-top:#7fb4d9;
  --sky-bottom:#3f7fb8;
  --white:#fff;
}
*{margin:0;padding:0;box-sizing:border-box}
html,body{width:851px;height:1200px;overflow:hidden;background:var(--white)}
body{position:relative;font-family:"Open Sans",Arial,sans-serif;color:var(--text)}
.abs{position:absolute}

/* header */
.brand{left:87px;top:20px;display:flex;align-items:center;gap:10px}
.brand-mark{width:34px;height:34px;background:var(--red)}
.brand-name{font-family:"Open Sans",Arial,sans-serif;font-weight:800;font-size:17px;line-height:19px;color:var(--ink);text-transform:uppercase;width:270px}
.contact-line{left:545px;display:flex;align-items:center;gap:10px}
.contact-phone{top:20px;font-size:16px;color:var(--red)}
.contact-mail{top:45px;font-size:8.5px;color:#333}
.contact-line svg{flex:none}

/* nav */
.nav{left:0;top:78px;width:851px;height:40px;background:linear-gradient(#e23a3f,var(--red) 55%,var(--red-dark));}
.nav ul{list-style:none;position:absolute;left:90px;top:0;height:40px;display:flex;align-items:center}
.nav li{font-size:9px;color:var(--white);text-transform:uppercase;height:40px;display:flex;align-items:center;padding:0 15px;border-left:1px solid rgba(255,255,255,.25)}
.nav li:first-child,.nav li:nth-child(2){border-left:none}
.nav li.active{background:linear-gradient(#3a3a3a,#080808);height:26px;border-radius:13px;padding:0 19px;margin-right:3px}

/* hero */
.hero{left:0;top:118px;width:851px;height:349px;background:linear-gradient(180deg,var(--sky-top),var(--sky-bottom) 70%,#2b5f93)}
.hero-title{left:521px;top:211px;font-family:"PT Sans Narrow",Arial,sans-serif;font-weight:700;font-size:17px;color:var(--white);text-transform:uppercase;letter-spacing:.1px}
.hero-rule{left:519px;top:235px;width:293px;height:1px;background:rgba(255,255,255,.7)}
.hero-copy{left:523px;top:244px;width:292px;font-size:8.6px;line-height:14.7px;color:#eaf2f9}
.hero-arrow{top:286px;width:30px;height:30px}

/* sections */
.section-title{font-family:"PT Sans Narrow",Arial,sans-serif;font-weight:700;font-size:16px;color:var(--ink)}
.section-title em{font-style:normal;color:var(--red)}
.rule{height:1px;background:var(--rule)}
.body-copy{font-size:8.4px;line-height:15px;color:var(--text)}
.btn{background:var(--red);color:var(--white);font-family:"PT Sans Narrow",Arial,sans-serif;font-weight:700;font-size:9px;display:flex;align-items:center;justify-content:center}
.expertise-list{list-style:none;left:614px;top:523px}
.expertise-list li{font-size:8px;line-height:17px;color:#333;text-transform:uppercase}
.expertise-list li::before{content:"›";margin-right:6px;color:#333}
.serve-title{left:108px;top:690px;font-size:14px;color:var(--red);font-family:"Open Sans",Arial,sans-serif}

/* sector cards */
.sector{width:156px}
.sector-image{width:156px;height:81px;border-radius:6px;border:1px solid #999;position:relative;overflow:hidden}
.sector-label{position:absolute;left:0;bottom:0;width:100%;height:20px;background:rgba(0,0,0,.5);color:var(--white);font-size:11px;line-height:20px;padding-left:9px}
.sector-copy{font-size:7.4px;line-height:9.8px;color:#666;margin:6px 2px 0;height:30px}
.sector-more{font-size:7.6px;color:var(--red);text-align:right;margin:7px 10px 0 0}
.sector-more::before{content:"";display:inline-block;width:5px;height:5px;border:1px solid #444;margin-right:5px;vertical-align:0}

/* footer */
.footer{left:0;top:1042px;width:851px;height:158px;background:linear-gradient(var(--footer-top),var(--footer-bottom));border-top:2px dotted #bbb}
.footer-title{left:108px;top:1056px;font-family:"PT Sans Narrow",Arial,sans-serif;font-size:14px;color:var(--white)}
.field{left:105px;width:195px;height:21px;background:var(--white);border:1px solid #bbb;font-size:7.4px;font-style:italic;color:#999;padding:5px 9px}
.subscribe{left:237px;top:1151px;width:62px;height:20px;border-radius:3px;background:linear-gradient(var(--red-light),var(--red-dark));border:1px solid #e66;font-size:8.6px;font-weight:600;color:var(--white);display:flex;align-items:center;justify-content:center}
.social{left:596px;top:1068px;display:flex;gap:10px}
.social span{width:17px;height:17px;border-radius:2px}
.copyright{right:100px;top:1107px;font-size:7.6px;color:#ccc}
</style>
</head>
<body>

<header>
  <div class="abs brand">
    <div class="brand-mark"></div>
    <div class="brand-name">Brightwater Delivery Partners</div>
  </div>
  <div class="abs contact-line contact-phone">
    <svg width="14" height="14" viewBox="0 0 14 14"><rect width="14" height="14" rx="2" fill="#777"/><path d="M4 3c1 0 1.5 2 1 2.5S5 7 6 8s2 1 2.5.5 2.5 0 2.5 1-1 1.5-2 1.5C6 11 3 8 3 5c0-1 .5-2 1-2z" fill="#fff"/></svg>
    <span>+61 0400 555 010</span>
  </div>
  <div class="abs contact-line contact-mail">
    <svg width="14" height="11" viewBox="0 0 14 11"><rect x=".5" y=".5" width="13" height="10" fill="#fff" stroke="#777"/><path d="M.5 .5 7 6l6.5-5.5" fill="none" stroke="#777"/></svg>
    <span>alex.morgan@brightwaterdeliverypartners-demo.com.au</span>
  </div>
</header>

<nav class="abs nav">
  <ul>
    <li class="active">Home</li>
    <li>About Us</li>
    <li>Expertise</li>
    <li>Knowledge</li>
    <li>Experience</li>
    <li>Projects</li>
    <li>Focus</li>
    <li>Contact</li>
    <li>Tesimonials</li>
  </ul>
</nav>

<section>
  <div class="abs hero" role="img" aria-label="Offshore drilling rig at dusk on a calm blue sea"></div>
  <h1 class="abs hero-title">Project Controls and Management Solutions</h1>
  <div class="abs hero-rule"></div>
  <p class="abs hero-copy">Cum sociis natoque penatibus et magnis dis parturient montes, nascetur ridiculus mus. In iaculis facilisis massa. Etiam eu urna. Sed porta.Cum sociis natoque penatibus et magnis dis parturient montes, nascetur ridiculus mus.</p>
  <svg class="abs hero-arrow" style="left:37px" viewBox="0 0 30 30"><circle cx="15" cy="15" r="15" fill="#2c3a4a"/><path d="M17 9l-6 6 6 6" fill="none" stroke="#fff" stroke-width="2.6"/></svg>
  <svg class="abs hero-arrow" style="left:782px" viewBox="0 0 30 30"><circle cx="15" cy="15" r="15" fill="#2c3a4a"/><path d="M13 9l6 6-6 6" fill="none" stroke="#fff" stroke-width="2.6"/></svg>
</section>

<section>
  <h2 class="abs section-title" style="left:110px;top:492px">Welcome to &nbsp;<em>BRIGHTWATER DELIVERY PARTNERS</em></h2>
  <div class="abs rule" style="left:110px;top:516px;width:463px"></div>
  <p class="abs body-copy" style="left:112px;top:522px;width:464px">I provide services to companies in the mining and oil and gas sector to enabling them to plan and manage their construction projects more effectively. This is achieved by evaluating the businesses practices and them implementing different tools and solutions.</p>
  <p class="abs body-copy" style="left:112px;top:581px;width:464px">My clients are then able to plan and deliver their projects, on time and within their budgets. I am able to provide services to both large and small scale businesses within Australian and Overseas. I offer my clients value by providing, exceptional skills and expertise at a competitive market rate.</p>
  <div class="abs btn" style="left:508px;top:639px;width:67px;height:19px">VIEW MORE &gt;&gt;</div>

  <h2 class="abs section-title" style="left:606px;top:492px"><em>Expertise</em></h2>
  <div class="abs rule" style="left:606px;top:516px;width:175px"></div>
  <ul class="abs expertise-list">
    <li>Project Management</li>
    <li>Project Controls</li>
    <li>Process Maping Approvals</li>
    <li>Solid Foundtations Through</li>
    <li>Systems Design and Implentation</li>
    <li>Resources</li>
    <li>Assisting Clients</li>
  </ul>
  <div class="abs btn" style="left:715px;top:639px;width:66px;height:19px">VIEW MORE &gt;&gt;</div>
</section>

<section>
  <h2 class="abs serve-title">WE SERVE</h2>
  <div class="abs rule" style="left:108px;top:711px;width:646px"></div>

  <article class="abs sector" style="left:108px;top:725px">
    <div class="sector-image" role="img" aria-label="Offshore oil platform against a blue sky" style="background:linear-gradient(#3d6fb0,#1d3d70)"><span class="sector-label">Oil &amp; Gas</span></div>
    <p class="sector-copy">Sed ut perspiciatis unde omnis iste natus error sit voluptatem accusantiumveritatis et quasi.sit accusantiumveritatis et quasi.</p>
    <p class="sector-more">Read More</p>
  </article>
  <article class="abs sector" style="left:272px;top:725px">
    <div class="sector-image" role="img" aria-label="Pile of colourful polished mineral stones" style="background:linear-gradient(135deg,#c0402a,#3b7fa8 50%,#d89a2e)"><span class="sector-label">Minerals &amp; Metals</span></div>
    <p class="sector-copy">Sed ut perspiciatis unde omnis iste natus error sit voluptatem accusantiumveritatis et quasi.sit accusantiumveritatis et quasi.</p>
    <p class="sector-more">Read More</p>
  </article>
  <article class="abs sector" style="left:435px;top:725px">
    <div class="sector-image" role="img" aria-label="Petrochemical refinery lit up at night" style="background:linear-gradient(#1c2f6a,#2b3f7a 60%,#b0782e)"><span class="sector-label">Petrochemical</span></div>
    <p class="sector-copy">Sed ut perspiciatis unde omnis iste natus error sit voluptatem accusantiumveritatis et quasi.sit accusantiumveritatis et quasi.</p>
    <p class="sector-more">Read More</p>
  </article>
  <article class="abs sector" style="left:599px;top:725px">
    <div class="sector-image" role="img" aria-label="Welding sparks in a manufacturing workshop" style="background:linear-gradient(135deg,#2a3f7e,#8aa0d0 50%,#6a3a3a)"><span class="sector-label">Manufacturing</span></div>
    <p class="sector-copy">Sed ut perspiciatis unde omnis iste natus error sit voluptatem accusantiumveritatis et quasi.sit accusantiumveritatis et quasi.</p>
    <p class="sector-more">Read More</p>
  </article>

  <article class="abs sector" style="left:108px;top:882px">
    <div class="sector-image" role="img" aria-label="Building under construction with scaffolding and crane" style="background:linear-gradient(#8aa6c4,#6b5a48)"><span class="sector-label">Building &amp; Construction</span></div>
    <p class="sector-copy">Sed ut perspiciatis unde omnis iste natus error sit voluptatem accusantiumveritatis et quasi.sit accusantiumveritatis et quasi.</p>
    <p class="sector-more">Read More</p>
  </article>
  <article class="abs sector" style="left:272px;top:882px">
    <div class="sector-image" role="img" aria-label="Globe wrapped in a glowing communications network" style="background:radial-gradient(circle at 50% 50%,#5cc0ea,#1660a8 70%)"><span class="sector-label">Telecommunications</span></div>
    <p class="sector-copy">Sed ut perspiciatis unde omnis iste natus error sit voluptatem accusantiumveritatis et quasi.sit accusantiumveritatis et quasi.</p>
    <p class="sector-more">Read More</p>
  </article>
  <article class="abs sector" style="left:435px;top:882px">
    <div class="sector-image" role="img" aria-label="High-speed train standing at a station platform" style="background:linear-gradient(#d8dadc,#8d8f92)"><span class="sector-label">Rail</span></div>
    <p class="sector-copy">Sed ut perspiciatis unde omnis iste natus error sit voluptatem accusantiumveritatis et quasi.sit accusantiumveritatis et quasi.</p>
    <p class="sector-more">Read More</p>
  </article>
  <article class="abs sector" style="left:599px;top:882px">
    <div class="sector-image" role="img" aria-label="Hand drafting a civil engineering plan with a pen" style="background:linear-gradient(90deg,#f1f1ee,#e0b070)"><span class="sector-label">Civil</span></div>
    <p class="sector-copy">Sed ut perspiciatis unde omnis iste natus error sit voluptatem accusantiumveritatis et quasi.sit accusantiumveritatis et quasi.</p>
    <p class="sector-more">Read More</p>
  </article>
</section>

<footer>
  <div class="abs footer"></div>
  <h2 class="abs footer-title">NEWSLETTER</h2>
  <div class="abs field" style="top:1087px">Name</div>
  <div class="abs field" style="top:1117px">your email address here..</div>
  <div class="abs subscribe">Subscribe &nbsp;›</div>
  <div class="abs social">
    <span style="background:#3b5b9a"></span>
    <span style="background:#3fb1e0"></span>
    <span style="background:#e8e8e8"></span>
    <span style="background:#f0a020"></span>
    <span style="background:#d11e1e"></span>
    <span style="background:#7a9aae"></span>
  </div>
  <p class="abs copyright">© 2013 brightwaterdeliverypartners-demo.com.au, All rights reserved</p>
</footer>

</body>
</html>
```